Business Recognition Design

We need a design for a recognition to be given to business leaders in our community.
The recognition shall be made on a brass plaque on wood panel background (picture attached, please use it as a background), and all drawing must be in vectors and only one color (black).
It should also have a logo on the top and signature on the right bottom.
The text is enclosed in DOC file.
Updates

Reason: just to be able to find the best solution

Reason: None of the suggestion is good enough. Logo in general is too big in comparison with the rest of the plate.

Industry/Entity Type

Business

Requirements
Must have
• - standard Windows font (or possibility to install the same font on Windows), as the name on the recognition shall be printed in the same font
Nice to have
• - some graphic element (in curves) representing achievements in business
- should look great :)

```html
<!DOCTYPE html>
<html lang="de">
<head>
<meta charset="utf-8">
<title>KapitalWerk Auszeichnung</title>
<link rel="stylesheet" href="https://fonts.googleapis.com/css2?family=Arimo:wght@400;700&display=swap">
<style>
  :root {
    --wood-dark: #3e1e0c;
    --wood-mid: #6a3a1c;
    --wood-light: #8a5230;
    --brass-light: #f6e089;
    --brass-mid: #e2bf4c;
    --brass-dark: #b78f22;
    --screw-light: #f3d66e;
    --screw-dark: #8a6414;
    --ink: #111111;
  }
  * { margin: 0; padding: 0; box-sizing: border-box; }
  html, body {
    width: 927px;
    height: 1200px;
    overflow: hidden;
    background: var(--wood-mid);
  }
  .plaque {
    position: relative;
    width: 927px;
    height: 1200px;
    background:
      linear-gradient(135deg, var(--wood-light) 0%, var(--wood-mid) 40%, var(--wood-dark) 100%);
    font-family: "Arimo", Arial, sans-serif;
    color: var(--ink);
  }
  .brass-plate {
    position: absolute;
    left: 57px;
    top: 57px;
    width: 813px;
    height: 1084px;
    background:
      linear-gradient(180deg, rgba(255,255,255,0.18) 0%, rgba(255,255,255,0) 45%, rgba(0,0,0,0.08) 100%),
      linear-gradient(120deg, var(--brass-dark) 0%, var(--brass-mid) 25%, var(--brass-light) 50%, var(--brass-mid) 75%, var(--brass-dark) 100%);
    box-shadow: 0 0 0 2px rgba(90,60,10,0.5), 3px 5px 10px rgba(0,0,0,0.45);
  }
  .screw {
    position: absolute;
    width: 32px;
    height: 32px;
    border-radius: 50%;
    background: radial-gradient(circle at 35% 35%, var(--screw-light) 0%, var(--brass-mid) 45%, var(--screw-dark) 100%);
    box-shadow: 1px 2px 3px rgba(0,0,0,0.5);
  }
  .screw.top-left { left: 72px; top: 59px; }
  .screw.top-right { left: 823px; top: 59px; }
  .screw.bottom-left { left: 72px; top: 1094px; }
  .screw.bottom-right { left: 823px; top: 1094px; }

  .centered {
    position: absolute;
    left: 0;
    width: 927px;
    text-align: center;
    white-space: nowrap;
  }
  .brand-name {
    top: 236px;
    font-size: 78px;
    font-weight: 700;
    letter-spacing: -1px;
    line-height: 1;
  }
  .brand-rule {
    position: absolute;
    left: 194px;
    top: 332px;
    width: 539px;
    height: 6px;
    background: var(--ink);
  }
  .headline {
    font-weight: 400;
    line-height: 1;
    letter-spacing: -0.5px;
  }
  .headline.award { top: 352px; font-size: 62px; }
  .headline.as { top: 430px; font-size: 55px; }
  .headline.role { top: 498px; font-size: 62px; }
  .headline.country { top: 573px; font-size: 58px; }

  .salutation {
    top: 706px;
    font-size: 27px;
  }
  .recipient {
    top: 758px;
    font-size: 56px;
    font-weight: 700;
  }
  .citation {
    position: absolute;
    left: 113px;
    width: 701px;
    top: 828px;
    font-size: 21.5px;
    line-height: 27.5px;
    text-align: center;
  }
  .place-date {
    position: absolute;
    left: 126px;
    top: 1016px;
    font-size: 23.5px;
  }
  .signatory {
    position: absolute;
    left: 710px;
    top: 1016px;
    font-size: 23.5px;
  }
</style>
</head>
<body>
<main class="plaque">
  <section class="brass-plate" aria-label="Messingschild"></section>
  <span class="screw top-left"></span>
  <span class="screw top-right"></span>
  <span class="screw bottom-left"></span>
  <span class="screw bottom-right"></span>

  <div class="centered brand-name">KapitalWerk</div>
  <div class="brand-rule"></div>

  <h1 class="centered headline award">AUSZEICHNUNG</h1>
  <p class="centered headline as">als herausragendster</p>
  <p class="centered headline role">UNTERNEHMER</p>
  <p class="centered headline country">Deutschlands 2013</p>

  <p class="centered salutation">für Herrn Dipl.-Kfm.</p>
  <p class="centered recipient">Max Muster</p>

  <p class="citation">Unter der Leitung von Herr Dipl.-Kfm. Max Muster hat sich die FIRMA GmbH im Jahr 2013 unter den ersten 5% der größten deutschen Wirtschaftsunternehmen platziert.</p>

  <p class="place-date">Gilching, 20. Juni 2013</p>
  <p class="signatory">Renate Kolbe</p>
</main>
</body>
</html>
```